RW Framewell Inc Business cards

We need business cards using our existing logo but slightly modified. Right now the logo says RW Loadbearing Masonry. We want to keep the RW part of the design, but replace the Structural Concrete portion with "FRAMEWELL". Please see the attached file.
Ideally this would be a blank template so we can add Different Names, titles, and phone numbers later.
On the one side we want only the logo and on the other side the detail. I'm attaching an example for you to see.
Please reach out with any other questions. Our address and other details will be given out once we find a design we like.

Target Market(s)

Construction Industry

```html
<!DOCTYPE html>
<html lang="en">
<head>
<meta charset="utf-8">
<title>RW Framewell Inc – Business Cards</title>
<link href="https://fonts.googleapis.com/css2?family=Roboto:wght@400;500;700&display=swap" rel="stylesheet">
<style>
  :root {
    --backdrop: #5b80ba;
    --brand-blue: #2f62a3;
    --card-white: #f4f4f4;
    --text-grey: #6b6b6b;
    --white: #ffffff;
  }
  * { margin: 0; padding: 0; box-sizing: border-box; }
  html, body {
    width: 1200px;
    height: 852px;
    overflow: hidden;
  }
  body {
    background: var(--backdrop);
    font-family: "Roboto", Arial, sans-serif;
  }
  .card-set {
    position: relative;
    width: 1200px;
    height: 852px;
  }
  .card {
    position: absolute;
    top: 277px;
    width: 520px;
    height: 297px;
    border-radius: 22px;
    overflow: hidden;
  }
  .card--front {
    left: 60px;
    background: var(--brand-blue);
    display: flex;
    align-items: center;
    justify-content: center;
  }
  .card--back {
    left: 620px;
    background: var(--card-white);
  }
  .wordmark {
    font-weight: 700;
    text-align: left;
    line-height: 1;
  }
  .wordmark__initials {
    display: block;
    font-size: 92px;
    letter-spacing: 2px;
  }
  .wordmark__name {
    display: block;
    font-size: 26px;
    letter-spacing: 7px;
    margin-top: 6px;
  }
  .card--front .wordmark { color: var(--white); }
  .card--back .wordmark {
    position: absolute;
    top: 34px;
    right: 44px;
    color: var(--brand-blue);
  }
  .card--back .wordmark__initials { font-size: 66px; }
  .card--back .wordmark__name { font-size: 19px; letter-spacing: 5px; margin-top: 4px; }
  .person {
    position: absolute;
    left: 34px;
    top: 120px;
  }
  .person__name {
    color: var(--brand-blue);
    font-size: 20px;
    font-weight: 700;
  }
  .person__title {
    color: var(--text-grey);
    font-size: 13px;
    margin-top: 3px;
  }
  .contact {
    position: absolute;
    left: 34px;
    bottom: 30px;
    list-style: none;
    color: var(--text-grey);
    font-size: 13px;
    line-height: 1.45;
  }
  .contact__item {
    display: flex;
    align-items: center;
    gap: 8px;
  }
  .contact__icon {
    width: 12px;
    height: 12px;
    flex: none;
    fill: var(--brand-blue);
  }
  .contact__item--plain { padding-left: 20px; }
  .web-tab {
    position: absolute;
    right: 0;
    bottom: 0;
    width: 215px;
    height: 70px;
    background: var(--brand-blue);
    border-top-left-radius: 22px;
    color: var(--white);
    font-size: 13px;
    font-weight: 700;
    display: flex;
    align-items: flex-start;
    justify-content: center;
    padding-top: 14px;
  }
</style>
</head>
<body>
  <main class="card-set">
    <section class="card card--front" aria-label="Card front">
      <div class="wordmark">
        <span class="wordmark__initials">RW</span>
        <span class="wordmark__name">FRAMEWELL</span>
      </div>
    </section>

    <section class="card card--back" aria-label="Card back">
      <div class="wordmark">
        <span class="wordmark__initials">RW</span>
        <span class="wordmark__name">FRAMEWELL</span>
      </div>

      <div class="person">
        <p class="person__name">Dana RW Porter</p>
        <p class="person__title">Managing Director</p>
      </div>

      <ul class="contact">
        <li class="contact__item">
          <svg class="contact__icon" viewBox="0 0 24 24" aria-hidden="true"><path d="M6.6 10.8a15.1 15.1 0 0 0 6.6 6.6l2.2-2.2a1 1 0 0 1 1-.25 11.4 11.4 0 0 0 3.6.57 1 1 0 0 1 1 1V20a1 1 0 0 1-1 1A17 17 0 0 1 3 4a1 1 0 0 1 1-1h3.5a1 1 0 0 1 1 1c0 1.25.2 2.45.57 3.6a1 1 0 0 1-.25 1z"/></svg>
          555-214-3080
        </li>
        <li class="contact__item">
          <svg class="contact__icon" viewBox="0 0 24 24" aria-hidden="true"><path d="M2 5h20v14H2z M3.5 6.5 12 12.5l8.5-6v-.1H3.5z" fill-rule="evenodd"/></svg>
          dana@framewell.com
        </li>
        <li class="contact__item contact__item--plain">18 Millbrook Rd., Fairhaven,</li>
        <li class="contact__item contact__item--plain">Oregon, US 970123</li>
      </ul>

      <div class="web-tab">www.framewellinc.com</div>
    </section>
  </main>
</body>
</html>
```